New, modern business card for growing audiology practice

We need a new business card for our audiology practice. Our logo and website have recently changed (more modern) and we want our business cards to reflect this change.
We conduct hearing tests, perform earwax removals, and fit & dispense hearing aids to our patients. We are a family owned practice in which the owner is the one who works directly with the patient. I have attached logos in various formats to use, as well as two ideas I found on this website; as well as a scanned copy of our current logo. Good luck!

Industry/Entity Type

Business

Contact Information for Business Card

Company name: Tolvera Hearing Center
Provider name: Peter Wolstenby, Au.D. F/NSB
Phone number: (440) 683-5127
Address: 837 W. Lindell Ave. Brenwick Falls, OH 44087
email: tolverahearing@postvane.com
website: tolverahearing.com

Colors
000000
aaaaaa
dbdbdb
cacaca
9bcb3c
afd23c
cadf82
b1b1b1

Requirements
Must have
• My card must include information in the "details" section. In the attached images, I found a few that I liked and I would like to model after - "brisky bouncin'" and "Sound Method Center".
• Must be horizontal.
• Must include logos provided. I uploaded them in various file formats and various ways.
• Must match logo font, if possible, if not, please get as close as you can.
Nice to have
• I really like the idea of having a color on one side with just the logo and company name and the contact information and provider name on the other side. I also really like the idea of having the main color dominating on the logo/company side with accent of that same color on the contact side of the card.
Should not have
• Must not be vertical.

```html
<!DOCTYPE html>
<html lang="en">
<head>
<meta charset="utf-8">
<title>Tolvera Hearing Center – Business Card</title>
<link rel="stylesheet" href="https://fonts.googleapis.com/css2?family=Lato:wght@400&family=Roboto+Condensed:wght@700&family=Roboto:wght@400;500&display=swap">
<style>
  :root {
    --green: #7aa83a;
    --green-soft: #9bcb3c;
    --ink: #111111;
    --text-grey: #555555;
    --card-white: #f4f4f4;
    --card-black: #000000;
    --divider: #b1b1b1;
    --backdrop: #dbdbdb;
    --white: #ffffff;
  }
  * { margin: 0; padding: 0; box-sizing: border-box; }
  html, body { width: 1200px; height: 960px; overflow: hidden; }
  body { background: var(--backdrop); position: relative; font-family: "Roboto", Arial, sans-serif; }

  .card { position: absolute; width: 600px; height: 343px; }
  .card--front { left: 314px; top: 113px; background: var(--card-white); }
  .card--back { left: 311px; top: 472px; background: var(--card-black); }

  .brand { position: absolute; display: flex; align-items: center; font-family: "Lato", "Gill Sans", sans-serif; font-weight: 400; white-space: nowrap; text-transform: uppercase; }
  .brand__dot { border-radius: 50%; background: var(--green); flex: none; }
  .card--front .brand { left: 46px; top: 161px; font-size: 17px; color: var(--ink); }
  .card--front .brand__dot { width: 14px; height: 14px; margin-right: 10px; }
  .card--back .brand { left: 0; right: 0; top: 154px; justify-content: center; font-size: 29px; color: var(--white); }
  .card--back .brand__dot { width: 22px; height: 22px; margin-right: 16px; }

  .divider { position: absolute; left: 318px; top: 84px; width: 1px; height: 178px; background: var(--divider); }

  .details { position: absolute; left: 349px; top: 90px; }
  .details__name { font-family: "Roboto Condensed", Arial, sans-serif; font-weight: 700; font-size: 21px; color: var(--green); line-height: 24px; }
  .details__credentials { font-weight: 500; font-size: 15px; color: var(--ink); line-height: 20px; margin-top: 1px; }
  .details__address { font-size: 14.5px; color: var(--text-grey); line-height: 18px; margin-top: 11px; }
  .contact-list { list-style: none; margin-top: 10px; }
  .contact-list li { display: flex; align-items: center; font-size: 14.5px; color: var(--text-grey); line-height: 19px; }
  .contact-list svg { width: 13px; height: 13px; margin-right: 10px; fill: var(--green); flex: none; }

  .website { position: absolute; left: 0; right: 0; top: 287px; text-align: center; font-size: 14px; letter-spacing: 5px; color: var(--white); }
  .website__name { color: var(--green-soft); }
</style>
</head>
<body>
  <section class="card card--front">
    <div class="brand"><span class="brand__dot"></span>Tolvera Hearing Center</div>
    <div class="divider"></div>
    <div class="details">
      <h1 class="details__name">PETER WOLSTENBY</h1>
      <p class="details__credentials">AU.D. F/NSB</p>
      <p class="details__address">837 W. Lindell Ave.<br>Brenwick Falls, OH 44087</p>
      <ul class="contact-list">
        <li><svg viewBox="0 0 16 16"><path d="M3.6 1.2l2.3 2.6-1.3 1.8c.9 2 2.4 3.5 4.3 4.4l1.8-1.3 2.6 2.3-1.4 2.2C7.3 13 3 8.7 1.4 2.6z"/></svg>(440) 683-5127</li>
        <li><svg viewBox="0 0 16 16"><path d="M1 3h14v1.2L8 9 1 4.2z M1 5.8l7 4.8 7-4.8V13H1z"/></svg>tolverahearing@postvane.com</li>
        <li><svg viewBox="0 0 16 16"><path d="M8 1a7 7 0 1 0 0 14A7 7 0 0 0 8 1zm0 1.8c.8.9 1.4 2.3 1.6 4.2H6.4C6.6 5.1 7.2 3.7 8 2.8zM2.9 9h2.5c.1 1.4.5 2.7 1 3.7A5.2 5.2 0 0 1 2.9 9zm0-2a5.2 5.2 0 0 1 3.5-3.7c-.5 1-.9 2.3-1 3.7zm5.1 6.2c-.8-.9-1.4-2.3-1.6-4.2h3.2c-.2 1.9-.8 3.3-1.6 4.2zm1.6-.5c.5-1 .9-2.3 1-3.7h2.5a5.2 5.2 0 0 1-3.5 3.7zM10.6 7c-.1-1.4-.5-2.7-1-3.7A5.2 5.2 0 0 1 13.1 7z"/></svg>tolverahearing.com</li>
      </ul>
    </div>
  </section>

  <section class="card card--back">
    <div class="brand"><span class="brand__dot"></span>Tolvera Hearing Center</div>
    <p class="website">www.<span class="website__name">tolverahearing</span>.com</p>
  </section>
</body>
</html>
```